Business card design

I need my logo on this card, things I need the card to have on it
licensed and insured.
owner operators Milo & Trent Halvorsen
my phone number 5083716254
Disaster Recovery, Storm Damage Restoration, Proactive Disaster Plan Management, Roof Repair/Restoration Structural Repair and Reconstruction, Emergency Boarding and Tarping Service, Perimeter Fencing, Emergency Tree Removal,

```html
<!DOCTYPE html>
<html lang="en">
<head>
<meta charset="utf-8">
<title>Halvorsen's Construction L.L.C – Business Card</title>
<link href="https://fonts.googleapis.com/css2?family=Questrial&family=Montserrat:wght@500;600&display=swap" rel="stylesheet">
<style>
  :root {
    --backdrop: #9b9b9b;
    --brand-blue: #1396ea;
    --brand-blue-deep: #0d86d6;
    --front-text: #cfe9fb;
    --card-white: #ffffff;
    --ink-grey: #6f7072;
  }
  * { margin: 0; padding: 0; box-sizing: border-box; }
  html, body {
    width: 1200px; height: 1200px; overflow: hidden;
    background: var(--backdrop);
    font-family: "Questrial", sans-serif;
  }
  .canvas { position: relative; width: 1200px; height: 1200px; }
  .card {
    position: absolute; left: 226px; width: 746px; height: 435px;
    border-radius: 28px; overflow: hidden;
  }
  .card--front { top: 95px; background: var(--brand-blue); }
  .card--back { top: 620px; background: var(--card-white); }

  /* front */
  .front-mark {
    position: absolute; left: 50%; top: 78px; transform: translateX(-50%);
    width: 84px; height: 84px; background: var(--brand-blue-deep); border-radius: 6px;
  }
  .front-name {
    position: absolute; left: 0; right: 0; top: 232px; text-align: center;
    color: var(--brand-blue-deep); font-size: 54px; letter-spacing: 1px; line-height: 1;
  }
  .front-name .sub { display: block; font-size: 20px; letter-spacing: 13px; margin-top: 12px; }
  .front-badge {
    position: absolute; left: 0; right: 0; top: 363px; text-align: center;
    color: var(--front-text); font-size: 21px; letter-spacing: 0.5px;
    display: flex; justify-content: center; align-items: center; gap: 6px;
  }

  /* back */
  .identity {
    position: absolute; left: 0; width: 376px; top: 122px; text-align: center;
  }
  .identity-mark {
    width: 66px; height: 66px; margin: 0 auto 18px; background: var(--brand-blue); border-radius: 4px;
  }
  .identity-name { color: var(--brand-blue); font-size: 36px; line-height: 1; letter-spacing: 0.5px; }
  .identity-name .sub { display: block; font-size: 13px; letter-spacing: 8px; margin-top: 6px; }
  .owners {
    margin-top: 14px; color: var(--ink-grey); font-family: "Montserrat", sans-serif;
    font-weight: 600; font-size: 18px;
  }
  .owners-role { color: var(--brand-blue); font-size: 13.5px; letter-spacing: 2px; margin-top: 6px; }
  .phone {
    margin-top: 4px; color: var(--ink-grey); font-size: 18px;
    display: flex; justify-content: center; align-items: center; gap: 5px;
  }
  .services {
    position: absolute; left: 374px; top: 95px; list-style: none;
    font-family: "Montserrat", sans-serif; font-weight: 600; font-size: 13.5px;
    color: var(--ink-grey); line-height: 26.3px;
  }
  .services li { position: relative; padding-left: 9px; }
  .services li::before {
    content: ""; position: absolute; left: 0; top: 12px; width: 3px; height: 3px;
    border-radius: 50%; background: var(--brand-blue);
  }
  .services li.continued::before { display: none; }
</style>
</head>
<body>
<div class="canvas">
  <section class="card card--front">
    <div class="front-mark"></div>
    <h1 class="front-name">HALVORSEN'S<span class="sub">CONSTRUCTION L.L.C</span></h1>
    <p class="front-badge">
      <svg width="18" height="16" viewBox="0 0 18 16" aria-hidden="true"><path d="M2 8.5 L7 13 L16 2" fill="none" stroke="currentColor" stroke-width="3" stroke-linecap="round" stroke-linejoin="round"/></svg>
      LICENSED &amp; INSURED
    </p>
  </section>

  <section class="card card--back">
    <div class="identity">
      <div class="identity-mark"></div>
      <h2 class="identity-name">HALVORSEN'S<span class="sub">CONSTRUCTION L.L.C</span></h2>
      <p class="owners">MILO &amp; TRENT HALVORSEN</p>
      <p class="owners-role">OWNER OPERATORS</p>
      <p class="phone">
        <svg width="15" height="15" viewBox="0 0 24 24" aria-hidden="true"><path fill="#1396ea" d="M6.6 10.8a15.1 15.1 0 0 0 6.6 6.6l2.2-2.2c.3-.3.7-.4 1-.2 1.1.4 2.3.6 3.6.6.6 0 1 .4 1 1V20c0 .6-.4 1-1 1A17 17 0 0 1 3 4c0-.6.4-1 1-1h3.5c.6 0 1 .4 1 1 0 1.3.2 2.5.6 3.6.1.3 0 .7-.2 1z"/></svg>
        (508) 371 - 6254
      </p>
    </div>
    <ul class="services">
      <li>DISASTER RECOVERY</li>
      <li>STORM DAMAGE RESTORATION</li>
      <li>PROACTIVE DISASTER PLAN MANAGEMENT</li>
      <li>ROOF REPAIR/RESTORATION</li>
      <li>STRUCTURAL REPAIR AND RECONSTRUCTION</li>
      <li>EMERGENCY BOARDING AND</li>
      <li class="continued">TARPING SERVICE</li>
      <li>PERIMETER FENCING</li>
      <li>EMERGENCY TREE REMOVAL</li>
    </ul>
  </section>
</div>
</body>
</html>
```